Trabworth Business Cards

We need a business card design for Trabworth Mining.

This is a B2B company that buys and sells large machinery tires within the coal mining industry. The design should the strong, crisp and masculine. I have uploaded the company logo and rough mock-up of what the back of the card should look like. the front of the card should have the same look/feel as the back. I need editable templates for both the front and the back of the card.

Color scheme should be grey/green/black

Contact information to include on the card:
Name: Dale Pembrose
Title: Managing Director
Phone: 555-314-2069
Address: 1187 Welford #3 Dallas, TX 75290
Email: Dale@Trabworth-example.com

I am also opening a contest for letterhead design. If you submit a business card design, please also submit a letterhead design with the same look/feel. The winner of the business card design will also will the letter head and be paid for both.

Target Market(s)

Procurement men/women in the coal mining industry

Industry/Entity Type

Coal Mining

```html
<!DOCTYPE html>
<html lang="en">
<head>
<meta charset="utf-8">
<title>Trabworth Mining Business Cards</title>
<link rel="stylesheet" href="https://fonts.googleapis.com/css2?family=Exo+2:wght@600;700&family=Open+Sans:wght@400;600&display=swap">
<style>
  :root {
    --bg: #e6e4e0;
    --card-black: #0b0b0b;
    --brand-green: #62b33f;
    --white: #ffffff;
    --soft-white: #e9e9e9;
  }
  * { margin: 0; padding: 0; box-sizing: border-box; }
  html, body { width: 1200px; height: 1024px; overflow: hidden; background: var(--bg); }
  .canvas { position: relative; width: 1200px; height: 1024px; }

  .card {
    position: absolute;
    background: var(--card-black);
    border-radius: 6px;
    overflow: hidden;
    box-shadow: 0 10px 28px rgba(0,0,0,0.25);
  }
  .card-front { left: 60px; top: 250px; width: 680px; height: 388px; }
  .card-back  { left: 810px; top: 200px; width: 330px; height: 578px; }

  .edge-art { position: absolute; inset: 0; width: 100%; height: 100%; }

  .wordmark { position: absolute; display: flex; align-items: center; gap: 12px; }
  .wordmark-square { width: 18px; height: 18px; background: var(--brand-green); }
  .wordmark-text { font-family: "Exo 2", sans-serif; font-weight: 700; color: var(--white); letter-spacing: 2px; line-height: 1; }
  .wordmark-sub {
    font-family: "Exo 2", sans-serif; font-weight: 600; color: var(--brand-green);
    letter-spacing: 14px; font-size: 11px; line-height: 1; margin-top: 6px;
  }

  .card-front .wordmark { left: 48px; top: 52px; }
  .card-front .wordmark-text { font-size: 36px; }

  .contact { position: absolute; left: 48px; top: 190px; font-family: "Open Sans", sans-serif; }
  .contact-name { color: var(--white); font-size: 26px; font-weight: 600; line-height: 1.15; }
  .contact-title { color: var(--brand-green); font-size: 17px; margin-bottom: 18px; }
  .contact-line { color: var(--soft-white); font-size: 15px; line-height: 1.6; }
  .contact-line .label { color: var(--brand-green); }

  .card-back .wordmark { left: 34px; top: 44px; }
  .card-back .wordmark-text { font-size: 28px; }
</style>
</head>
<body>
<main class="canvas">

  <section class="card card-front" aria-label="Business card front">
    <svg class="edge-art" viewBox="0 0 680 388" aria-hidden="true">
      <path d="M612 0 H680 V150 H640 Q612 150 612 178 Z" fill="var(--white)"/>
      <path d="M612 196 L680 170 V388 H560 L612 330 Z" fill="var(--brand-green)"/>
    </svg>
    <div class="wordmark">
      <span class="wordmark-square"></span>
      <div>
        <div class="wordmark-text">TRABWORTH</div>
        <div class="wordmark-sub">MINING</div>
      </div>
    </div>
    <div class="contact">
      <div class="contact-name">Dale Pembrose</div>
      <div class="contact-title">Managing Director</div>
      <div class="contact-line"><span class="label">P:</span> 555-314-2069</div>
      <div class="contact-line"><span class="label">A:</span> 1187 Welford #3 Dallas, TX 75290</div>
      <div class="contact-line"><span class="label">E:</span> Dale@Trabworth-example.com</div>
    </div>
  </section>

  <section class="card card-back" aria-label="Business card back">
    <svg class="edge-art" viewBox="0 0 330 578" aria-hidden="true">
      <polygon points="0,210 330,150 330,205 0,265" fill="var(--brand-green)"/>
      <polygon points="235,390 330,470 330,578 300,578" fill="var(--brand-green)"/>
    </svg>
    <div class="wordmark">
      <span class="wordmark-square"></span>
      <div>
        <div class="wordmark-text">TRABWORTH</div>
        <div class="wordmark-sub">MINING</div>
      </div>
    </div>
  </section>

</main>
</body>
</html>
```